Quillmere Supply Chain and Logistic Consulting

Please review the attached Business Card. I want as close to this card with the colors, fonts, and quality of the card as possible. The attached compass should replace the deer head on both sides of the card and the text should say:

Backside
Compass JPEG
Quillmere SC&L
A Supply Chain and Logistics Consulting Company

Frontside
Quillmere SC&L
Ray Falkner - Corvale Harbor
President
____________________________________
(555) 314-9027
QuillmereSCL@Examplemail.com
_____________________________________

Bottom Front Side

Target Market(s)

Businesses

Contact Information for Business Card

Backside
Compass JPEG
Quillmere SC&L

Frontside
Quillmere SC&L
President
(555) 314-9027
QuillmereSCL@Examplemail.com

Bottom Front Side

Font styles to use
Serif
Script

Colors

Designer to choose colors to be used in the design.

Requirements
Must have
• See attached card for reference
Nice to have
Should not have

```html
<!DOCTYPE html>
<html lang="en">
<head>
<meta charset="utf-8">
<title>Quillmere SC&amp;L — Business Card</title>
<link rel="stylesheet" href="https://fonts.googleapis.com/css2?family=Cinzel:wght@400;500&family=Tinos:wght@400;700&display=swap">
<style>
  :root {
    --bg: #e4e4e6;
    --navy: #062a4c;
    --ink-light: #ffffff;
    --rule: rgba(255, 255, 255, 0.35);
    --emblem-light: #f4f6f9;
    --emblem-mid: #c9d3e0;
    --emblem-dark: #4d6a8f;
  }
  * { margin: 0; padding: 0; box-sizing: border-box; }
  html, body { width: 1200px; height: 900px; overflow: hidden; }
  body { background: var(--bg); position: relative; font-family: "Tinos", "Times New Roman", serif; color: var(--ink-light); }

  .card {
    position: absolute;
    width: 525px;
    height: 300px;
    background: var(--navy);
    border-radius: 22px;
    overflow: hidden;
    box-shadow: 0 14px 28px rgba(0, 0, 0, 0.22);
  }

  /* Back side */
  .card--back { left: 90px; top: 120px; display: flex; flex-direction: column; align-items: center; justify-content: center; }
  .card--back .brand-dot {
    width: 92px; height: 92px; border-radius: 50%;
    background: var(--emblem-light);
    margin-bottom: 26px;
  }
  .card--back .brand-name {
    font-family: "Cinzel", "Times New Roman", serif;
    font-size: 27px; letter-spacing: 2px; font-weight: 400;
  }
  .card--back .tagline {
    font-family: "Cinzel", "Times New Roman", serif;
    font-size: 15px; letter-spacing: 1px; margin-top: 10px;
  }

  /* Front side */
  .card--front { left: 585px; top: 480px; }
  .card--front .emblem-area { position: absolute; left: -200px; top: 70px; width: 430px; height: 430px; }
  .card--front .details { position: absolute; left: 238px; top: 22px; right: 22px; }
  .card--front .brand-name {
    font-family: "Cinzel", "Times New Roman", serif;
    font-size: 25px; letter-spacing: 1.5px; font-weight: 400; text-align: right;
    white-space: nowrap;
  }
  .card--front .locale { font-weight: 700; font-size: 17px; text-align: right; margin-top: 2px; white-space: nowrap; }
  .rule { height: 1px; background: var(--rule); margin: 11px 0; }
  .person-name { font-weight: 700; font-size: 16px; }
  .person-role { font-size: 12px; margin-top: 1px; }
  .contact-list { list-style: none; margin-top: 9px; }
  .contact-list li { display: flex; align-items: center; gap: 7px; font-size: 15px; line-height: 1.35; white-space: nowrap; }
  .contact-list svg { width: 13px; height: 13px; fill: var(--ink-light); flex: none; }
  .card--front .tagline {
    font-family: "Cinzel", "Times New Roman", serif;
    font-size: 14px; letter-spacing: 0.8px; line-height: 1.3;
  }
</style>
</head>
<body>

  <section class="card card--back" aria-label="Business card, back">
    <div class="brand-dot"></div>
    <h1 class="brand-name">QUILLMERE SC&amp;L</h1>
    <p class="tagline">A Supply Chain and Logistics Consulting Company</p>
  </section>

  <section class="card card--front" aria-label="Business card, front">
    <svg class="emblem-area" viewBox="0 0 430 430" role="img" aria-label="Large compass rose emblem on a white disc">
      <defs>
        <radialGradient id="emblemFill" cx="50%" cy="50%" r="50%">
          <stop offset="0" stop-color="#4d6a8f"/>
          <stop offset="0.35" stop-color="#c9d3e0"/>
          <stop offset="1" stop-color="#f4f6f9"/>
        </radialGradient>
      </defs>
      <circle cx="215" cy="215" r="215" fill="url(#emblemFill)"/>
    </svg>

    <div class="details">
      <h1 class="brand-name">QUILLMERE SC&amp;L</h1>
      <p class="locale">Ray Falkner - Corvale Harbor</p>
      <div class="rule"></div>
      <p class="person-name">Ray Falkner</p>
      <p class="person-role">President</p>
      <ul class="contact-list">
        <li>
          <svg viewBox="0 0 16 16" aria-hidden="true"><path d="M3 1h3l1.5 4-2 1.3a9 9 0 0 0 4.2 4.2L11 8.5l4 1.5v3a2 2 0 0 1-2 2A12 12 0 0 1 1 3a2 2 0 0 1 2-2z"/></svg>
          (555) 314-9027
        </li>
        <li>
          <svg viewBox="0 0 16 16" aria-hidden="true"><path d="M1 3h14v10H1z M1.8 3.8 8 8.6l6.2-4.8" stroke="#062a4c" stroke-width="1.2"/></svg>
          QuillmereSCL@Examplemail.com
        </li>
      </ul>
      <div class="rule"></div>
      <p class="tagline">A Supply Chain and Logistics<br>Consulting Company</p>
    </div>
  </section>

</body>
</html>
```